Redesign of business card for Cedar Ridge Mechanical

We are looking for a new design for our business cards for Cedar Ridge Mechanical. We are a plumbing & HVAC construction company, operating on the West Coast of Canada and USA. Logo attached.
Industry/Entity Type
Construction - Plumbing & HVAC
Contact Information for Business Card
Name, address, phone numbers, email, website address
Look and feel
Each slider illustrates characteristics of the customer's brand and the style your logo design should communicate.

```html
<!DOCTYPE html>
<html lang="en">
<head>
<meta charset="utf-8">
<title>Cedar Ridge Mechanical – Business Card</title>
<link href="https://fonts.googleapis.com/css2?family=Poppins:wght@300;400;600&display=swap" rel="stylesheet">
<style>
  :root{
    --stage:#1f1f21;
    --card:#222326;
    --ink:#ffffff;
    --muted:#d9d9db;
    --emboss:#3a3b3f;
    --band:#ffffff;
    --band-ink:#1c1c1e;
  }
  *{margin:0;padding:0;box-sizing:border-box}
  html,body{width:1200px;height:711px;overflow:hidden;background:var(--stage);font-family:'Poppins',sans-serif}
  .stage{position:relative;width:1200px;height:711px;display:flex;align-items:center;justify-content:center;gap:40px}
  .card{position:relative;width:540px;height:309px;background:var(--card);overflow:hidden;box-shadow:0 10px 30px rgba(0,0,0,.45)}
  /* front */
  .front-mark{position:absolute;inset:0;display:flex;align-items:center;justify-content:center;gap:14px}
  .front-mark .square{width:26px;height:26px;background:var(--emboss)}
  .front-mark .brand{font-size:30px;font-weight:600;color:var(--emboss);letter-spacing:.5px}
  /* back */
  .back-brand{position:absolute;left:32px;top:96px;display:flex;align-items:center;gap:10px}
  .back-brand .square{width:18px;height:18px;background:var(--ink)}
  .back-brand .brand{font-size:19px;font-weight:600;color:var(--ink);line-height:1.15;width:190px}
  .divider{position:absolute;left:262px;top:40px;width:1px;height:170px;background:#8a8a8e}
  .contact{position:absolute;left:290px;top:48px;color:var(--ink)}
  .contact .name{font-size:24px;line-height:1.1;font-weight:300}
  .contact .name b{font-weight:600}
  .contact .role{font-size:12px;font-weight:400;margin-top:2px;color:var(--muted)}
  .contact ul{list-style:none;margin-top:18px}
  .contact li{display:flex;align-items:center;gap:8px;font-size:12px;font-weight:300;margin-bottom:5px}
  .contact svg{width:12px;height:12px;fill:var(--ink)}
  .band{position:absolute;left:0;right:0;top:242px;height:28px;background:var(--band);display:flex;align-items:center;padding-left:34px;z-index:1}
  .band .address{font-size:12.5px;color:var(--band-ink);font-weight:400}
  .band-tab{position:absolute;right:0;top:206px;width:128px;height:64px;background:var(--band);display:flex;align-items:center;justify-content:center;z-index:2}
  .band-tab .brand{font-size:11px;font-weight:600;color:var(--band-ink);text-align:center;line-height:1.25}
</style>
</head>
<body>
<main class="stage">
  <section class="card card-front" aria-label="Card front">
    <div class="front-mark">
      <span class="square"></span>
      <span class="brand">Cedar Ridge Mechanical</span>
    </div>
  </section>

  <section class="card card-back" aria-label="Card back">
    <div class="back-brand">
      <span class="square"></span>
      <span class="brand">Cedar Ridge Mechanical</span>
    </div>
    <div class="divider"></div>
    <div class="contact">
      <p class="name"><b>Marta</b> Kovar</p>
      <p class="role">Founder &amp; CEO</p>
      <ul>
        <li><svg viewBox="0 0 24 24"><path d="M6.6 10.8a15.1 15.1 0 0 0 6.6 6.6l2.2-2.2a1 1 0 0 1 1-.25 11.4 11.4 0 0 0 3.6.57 1 1 0 0 1 1 1V20a1 1 0 0 1-1 1A17 17 0 0 1 3 4a1 1 0 0 1 1-1h3.5a1 1 0 0 1 1 1c0 1.250.2 2.450.57 3.6a1 1 0 0 1-.25 1z"/></svg>(555) 214-6083</li>
        <li><svg viewBox="0 0 24 24"><path d="M20 4H4a2 2 0 0 0-2 2v12a2 2 0 0 0 2 2h16a2 2 0 0 0 2-2V6a2 2 0 0 0-2-2zm0 4-8 5-8-5V6l8 5 8-5z"/></svg>info@yourwebsite.com</li>
        <li><svg viewBox="0 0 24 24"><path d="M12 2a10 10 0 1 0 0 20 10 10 0 0 0 0-20zm6.9 6h-2.9a15.7 15.7 0 0 0-1.4-3.6A8 8 0 0 1 18.9 8zM12 4c.8 1.2 1.5 2.5 1.9 4h-3.8c.4-1.5 1.1-2.8 1.9-4zM4.3 14a8.2 8.2 0 0 1 0-4h3.4a16.5 16.5 0 0 0 0 4zm.8 2h2.9c.3 1.3.8 2.5 1.4 3.6A8 8 0 0 1 5.1 16zM8 8H5.1a8 8 0 0 1 4.3-3.6C8.8 5.5 8.3 6.7 8 8zm4 12c-.8-1.2-1.5-2.5-1.9-4h3.8c-.4 1.5-1.1 2.8-1.9 4zm2.3-6H9.7a14.7 14.7 0 0 1 0-4h4.6a14.7 14.7 0 0 1 0 4zm.3 5.6c.6-1.1 1.1-2.3 1.4-3.6h2.9a8 8 0 0 1-4.3 3.6zm1.7-5.6a16.5 16.5 0 0 0 0-4h3.4a8.2 8.2 0 0 1 0 4z"/></svg>www.yourwebsite.com</li>
      </ul>
    </div>
    <div class="band"><span class="address">1840 Harbor Ln. Suite 310 Portland, OR 97205</span></div>
    <div class="band-tab"><span class="brand">Cedar Ridge<br>Mechanical</span></div>
  </section>
</main>
</body>
</html>
```